Career Development Skills | Business Card & Logo Design

We are looking for a business card including logo design for a new Sydney based business called 'Bright Pathwork'.
We offer a range of services that focus on building the Employability or Employment skills for individuals focusing on job seekers and those interested in building skills required to develop their career. Employability skills are required not only to gain employment, but also to progress within an organisation so as to achieve one's potential.
Updates
Target Market(s)
Our client targets include corporates and govt agencies looking to build skills within their current employee base or assist staff in the transition between roles or workplaces.
Industry/Entity Type
Business
Look and feel
Each slider illustrates characteristics of the customer's brand and the style your logo design should communicate.

```html
<!DOCTYPE html>
<html lang="en">
<head>
<meta charset="utf-8">
<title>Bright Pathwork – Business Card</title>
<link href="https://fonts.googleapis.com/css2?family=Cinzel:wght@700&family=Roboto+Condensed:wght@400;700&display=swap" rel="stylesheet">
<style>
  :root {
    --backdrop: #1b1b1b;
    --card-dark-top: #2e2e2e;
    --card-dark-bottom: #121212;
    --card-light-top: #d9dadb;
    --card-light-bottom: #f6f6f6;
    --teal: #1a9aa3;
    --navy: #163a86;
    --silver: #b9bcbf;
    --rule: #8a8c8f;
    --contact-blue: #233d8c;
    --contact-grey: #6d6f72;
  }
  * { margin: 0; padding: 0; box-sizing: border-box; }
  html, body { width: 1200px; height: 858px; overflow: hidden; }
  body {
    position: relative;
    background: var(--backdrop);
    font-family: "Roboto Condensed", sans-serif;
  }
  .card {
    position: absolute;
    width: 545px;
    height: 334px;
    box-shadow: 0 6px 18px rgba(0,0,0,.6);
  }
  .card--front { top: 71px; background: linear-gradient(160deg, var(--card-dark-top), var(--card-dark-bottom) 60%); }
  .card--teal { left: 43px; }
  .card--navy { left: 614px; }
  .logo-lockup {
    position: absolute;
    top: 112px; left: 0; right: 0;
    display: flex; align-items: center; justify-content: center; gap: 12px;
  }
  .logo-lockup__dot { width: 18px; height: 18px; border-radius: 50%; background: var(--silver); }
  .logo-lockup__name {
    font-family: "Cinzel", serif; font-weight: 700; font-size: 26px;
    color: var(--silver); letter-spacing: 1px; white-space: nowrap;
  }
  .front-rule {
    position: absolute; top: 196px; left: 120px; width: 305px; height: 1px;
    background: linear-gradient(90deg, transparent, var(--rule) 30%, var(--rule) 70%, transparent);
  }
  .wordmark {
    position: absolute; top: 206px; left: 0; right: 0; text-align: center;
    font-family: "Cinzel", serif; font-weight: 700; font-size: 24px; letter-spacing: 1px;
    white-space: nowrap;
  }
  .card--teal .wordmark { color: var(--teal); }
  .card--navy .wordmark { color: var(--navy); }

  .card--back {
    left: 292px; top: 460px; width: 542px; height: 331px;
    background: linear-gradient(90deg, var(--card-light-top), var(--card-light-bottom));
    overflow: hidden;
  }
  .back-rule { position: absolute; left: 119px; top: 74px; width: 1px; height: 190px; background: var(--rule); }
  .contact { position: absolute; left: 141px; top: 72px; font-size: 13px; line-height: 16px; white-space: nowrap; }
  .contact__identity { color: var(--contact-blue); font-weight: 700; }
  .contact__address { margin-top: 22px; color: var(--contact-grey); }
  .contact__lines { margin-top: 20px; }
  .contact__line { display: flex; align-items: baseline; }
  .contact__label {
    display: flex; width: 85px; margin-right: 4px; overflow: hidden;
    color: var(--contact-blue); font-weight: 700;
  }
  .contact__leader { flex: 1; overflow: hidden; margin-left: 3px; letter-spacing: -0.5px; }
  .contact__value { color: var(--contact-grey); font-weight: 700; }
  .back-mark { position: absolute; right: -30px; top: 30px; }
</style>
</head>
<body>
  <section class="card card--front card--teal">
    <div class="logo-lockup"><span class="logo-lockup__dot"></span><span class="logo-lockup__name">Bright Pathwork</span></div>
    <div class="front-rule"></div>
    <div class="wordmark">BRIGHT PATHWORK</div>
  </section>

  <section class="card card--front card--navy">
    <div class="logo-lockup"><span class="logo-lockup__dot"></span><span class="logo-lockup__name">Bright Pathwork</span></div>
    <div class="front-rule"></div>
    <div class="wordmark">BRIGHT PATHWORK</div>
  </section>

  <section class="card card--back">
    <div class="back-rule"></div>
    <div class="contact">
      <div class="contact__identity">
        <div>Daniel Hartley - Director</div>
        <div>Brightpathwork.com.au</div>
        <div>daniel@brightpathwork.com.au</div>
      </div>
      <div class="contact__address">
        <div>Level 14</div>
        <div>Harbour Point Tower 3</div>
        <div>118 &nbsp; Kent Street</div>
        <div>Harbour Point, Sydney 2000</div>
      </div>
      <div class="contact__lines">
        <div class="contact__line"><span class="contact__label">Tel<span class="contact__leader">------------------------------</span></span><span class="contact__value">(02) 95550142</span></div>
        <div class="contact__line"><span class="contact__label">Fax<span class="contact__leader">------------------------------</span></span><span class="contact__value">(02) 95550187</span></div>
      </div>
    </div>
    <svg class="back-mark" width="160" height="160" viewBox="0 0 160 160" aria-hidden="true">
      <defs>
        <radialGradient id="markShade" cx="40%" cy="40%" r="60%">
          <stop offset="0" stop-color="#e4e5e6"/>
          <stop offset="1" stop-color="#b4b6b8"/>
        </radialGradient>
      </defs>
      <circle cx="80" cy="80" r="70" fill="url(#markShade)"/>
    </svg>
  </section>
</body>
</html>
```